Album Cover for upcoming release

Hi, I need an album cover for a song that I’ll be releasing soon. The album cover must contain the title of the song, which is:

Carry the Moon (remix)

The album cover must also contain the artist name:

Owen Tarrick

The song is a remix of a song that I released in late-May called “Carry the Moon.” I wrote the original song for my wife. If you’re interested, please give it a listen on Velvo Tunes or Rumblewave under the artist Owen Tarrick. Here’s a Rumblewave link to the original song (it already has more than 175,000 streams):

https://play.rumblewave.example/track/7RbTqZ82KXN3pLmWcVoHeF?si=ztGd4NfQxWYb9uRsEoPaMc

The remix is VERY, VERY different! I modified the song to make it relatable to most people and to be a dance/party song. Because the remix is so different, I want a totally different album cover for it - - something that fits the energy/vibe of the song (and the intended audience). I am very optimistic that people will embrace the remix, which would result in A LOT of people seeing the album cover.

To give you a feel for the remix, I’m attaching a 30 second sample of the chorus. Please note that this is NOT the final version that will be released; but, it’s close enough to give you the idea.

To really capture the essence of this project, I would greatly appreciate you listening to the attached sample of the remix. Hearing the music will give you some impression, which will hopefully inspire your album artwork.

Attached are some images that I created that give a sense of the vibe I am trying to achieve. Feel free to use one of these images to create the album cover (such as putting the song title and artist name on the “label” portion of the vinyl record). But, you are NOT required to use one os these images.
Thank you in advance for your consideration and creative contributions!

Target Market(s)

Dance and party crowd; night clubs, sporting events, weddings

Font styles to use
Sans Serif

Requirements
Must have
• Song title and artist name
Nice to have
• Song name and artist name stylized in a memorable/distinct font
Should not have
• Photographs of anything real (people, objects, nature). Animated can be fine

```html
<!DOCTYPE html>
<html lang="en">
<head>
<meta charset="utf-8">
<title>Owen Tarrick – Carry the Moon (Remix)</title>
<link rel="stylesheet" href="https://fonts.googleapis.com/css2?family=Bebas+Neue&family=Permanent+Marker&family=Syncopate:wght@700&display=swap">
<style>
  :root {
    --sky-top: #b0443f;
    --sky-low: #c9503a;
    --sun-core: #ffd23a;
    --sun-edge: #f39a1e;
    --sea-light: #3f5fc4;
    --sea-mid: #27357f;
    --sea-deep: #101a44;
    --ink-white: #ffffff;
    --shadow-dark: rgba(0, 0, 0, 0.85);
    --glow-magenta: #d23cff;
  }
  html, body {
    margin: 0;
    padding: 0;
    width: 1200px;
    height: 1200px;
    overflow: hidden;
    background: var(--sea-deep);
  }
  .cover {
    position: relative;
    width: 1200px;
    height: 1200px;
    overflow: hidden;
  }
  .cover-art,
  .cover-type {
    position: absolute;
    inset: 0;
    width: 1200px;
    height: 1200px;
    display: block;
  }
  .artist-name {
    font-family: "Syncopate", sans-serif;
    font-weight: 700;
    font-size: 40px;
    fill: var(--ink-white);
  }
  .song-title {
    font-family: "Permanent Marker", cursive;
    font-size: 176px;
    fill: var(--ink-white);
  }
  .remix-tag {
    font-family: "Bebas Neue", sans-serif;
    font-size: 545px;
    fill: rgba(210, 60, 255, 0.12);
    stroke: var(--ink-white);
    stroke-width: 4;
  }
</style>
</head>
<body>
<main class="cover">
  <svg class="cover-art" viewBox="0 0 1200 1200" role="img" aria-label="Illustrated sunset over a rippling ocean with a large glowing sun and a vinyl record floating on the water">
    <defs>
      <linearGradient id="sky" x1="0" y1="0" x2="0" y2="1">
        <stop offset="0" stop-color="var(--sky-top)"/>
        <stop offset="1" stop-color="var(--sky-low)"/>
      </linearGradient>
      <linearGradient id="sea" x1="0" y1="0" x2="0" y2="1">
        <stop offset="0" stop-color="var(--sea-light)"/>
        <stop offset="0.45" stop-color="var(--sea-mid)"/>
        <stop offset="1" stop-color="var(--sea-deep)"/>
      </linearGradient>
      <radialGradient id="sunGlow" cx="0.5" cy="0.5" r="0.5">
        <stop offset="0" stop-color="var(--sun-core)"/>
        <stop offset="0.75" stop-color="var(--sun-edge)" stop-opacity="0.85"/>
        <stop offset="1" stop-color="var(--sun-edge)" stop-opacity="0"/>
      </radialGradient>
    </defs>
    <rect x="0" y="0" width="1200" height="425" fill="url(#sky)"/>
    <rect x="0" y="425" width="1200" height="775" fill="url(#sea)"/>
    <ellipse cx="880" cy="330" rx="270" ry="260" fill="url(#sunGlow)"/>
  </svg>

  <svg class="cover-type" viewBox="0 0 1200 1200">
    <defs>
      <filter id="titleShadow" x="-10%" y="-30%" width="120%" height="160%">
        <feDropShadow dx="-18" dy="22" stdDeviation="6" flood-color="var(--shadow-dark)"/>
      </filter>
      <filter id="neonGlow" x="-10%" y="-10%" width="120%" height="120%">
        <feGaussianBlur in="SourceGraphic" stdDeviation="7" result="blur"/>
        <feFlood flood-color="var(--glow-magenta)"/>
        <feComposite in2="blur" operator="in" result="glow"/>
        <feMerge>
          <feMergeNode in="glow"/>
          <feMergeNode in="glow"/>
          <feMergeNode in="SourceGraphic"/>
        </feMerge>
      </filter>
    </defs>

    <text class="artist-name" x="236" y="152" textLength="727" lengthAdjust="spacing">OWEN TARRICK</text>

    <text class="song-title" x="104" y="520" textLength="1000" lengthAdjust="spacingAndGlyphs" filter="url(#titleShadow)">Carry the Moon</text>

    <text class="remix-tag" x="242" y="981" textLength="795" lengthAdjust="spacingAndGlyphs" filter="url(#neonGlow)">REMIX</text>
  </svg>
</main>
</body>
</html>
```